DELCOURT ROOFING YARD SIGN

We need a yard sign to put in our customers' yards when we are roofing their home.
Delcourt Roofing
417 Tobin Rd
Lake Charles LA 70615
phone: 337-555-0182

Maybe some verbiage like "Your Hometown Roofing Experts"
or
"Family Owned Since 1956"

```html
<!DOCTYPE html>
<html lang="en">
<head>
<meta charset="utf-8">
<title>Delcourt Roofing Yard Sign</title>
<link rel="stylesheet" href="https://fonts.googleapis.com/css2?family=Fraunces:opsz,wght@9..144,700;9..144,900&family=Marcellus&display=swap">
<style>
  :root {
    --page-light: #c4c4c4;
    --page-mid: #6e6e6e;
    --page-dark: #1e1e1e;
    --sign-dark: #1b1b1b;
    --band-black: #0c0c0c;
    --band-white: #ffffff;
    --band-silver: #cbc8c6;
    --ink: #0a0a0a;
    --paper: #ffffff;
    --ring: #b9b9b9;
  }
  * { margin: 0; padding: 0; box-sizing: border-box; }
  html, body { width: 1200px; height: 1174px; overflow: hidden; }
  body {
    background: linear-gradient(100deg, var(--page-light) 0%, var(--page-mid) 40%, var(--page-dark) 85%);
    position: relative;
  }
  .yard-sign {
    position: absolute;
    left: 45px;
    top: 424px;
    width: 1110px;
    height: 325px;
    background: var(--sign-dark);
    box-shadow: 0 14px 30px rgba(0,0,0,0.45);
  }
  .band {
    position: absolute;
    left: 300px;
    right: 0;
    display: flex;
    flex-direction: column;
    align-items: center;
    justify-content: center;
    padding-left: 80px;
  }
  .band-name {
    top: 0;
    height: 113px;
    background: linear-gradient(90deg, var(--sign-dark) 0%, var(--band-white) 38%, var(--band-white) 100%);
  }
  .band-tagline {
    top: 113px;
    height: 129px;
    background: linear-gradient(90deg, var(--sign-dark) 0%, var(--band-black) 30%, var(--band-black) 100%);
  }
  .band-contact {
    top: 242px;
    height: 83px;
    background: linear-gradient(90deg, var(--sign-dark) 0%, var(--band-silver) 40%, #bfbcbb 100%);
  }
  .company-name {
    font-family: "Fraunces", Georgia, serif;
    font-weight: 900;
    font-size: 62px;
    letter-spacing: 0.5px;
    color: var(--ink);
    line-height: 1;
    white-space: nowrap;
  }
  .tagline {
    font-family: "Marcellus", "Times New Roman", serif;
    font-size: 46px;
    letter-spacing: 2px;
    color: var(--paper);
    line-height: 1.05;
    text-align: center;
    text-transform: uppercase;
  }
  .contact {
    font-family: "Fraunces", Georgia, serif;
    font-weight: 700;
    font-size: 27px;
    color: var(--ink);
    line-height: 1.15;
    text-align: center;
    white-space: nowrap;
  }
  .emblem {
    position: absolute;
    left: 20px;
    top: 0;
    width: 326px;
    height: 326px;
    border-radius: 50%;
    background: var(--paper);
    border: 3px solid var(--ring);
    display: flex;
    align-items: center;
    justify-content: center;
    box-shadow: 8px 6px 22px rgba(0,0,0,0.5);
  }
  .emblem-name {
    font-family: "Fraunces", Georgia, serif;
    font-weight: 700;
    font-size: 34px;
    line-height: 1.15;
    color: var(--ink);
    text-align: center;
  }
</style>
</head>
<body>
  <section class="yard-sign">
    <div class="band band-name">
      <h1 class="company-name">DELCOURT ROOFING</h1>
    </div>
    <div class="band band-tagline">
      <p class="tagline">Your Hometown<br>Roofing Experts</p>
    </div>
    <div class="band band-contact">
      <p class="contact">417 Tobin Rd, Lake Charles LA 70615<br>Phone: 337-555-0182</p>
    </div>
    <div class="emblem">
      <p class="emblem-name">Delcourt<br>Roofing</p>
    </div>
  </section>
</body>
</html>
```